Loom Harbor needs a website

I sell rugs and carpet on my website, loomharborfloors.example. I need help with the site design to make it "pop". The logo in the header has been designed and I want the site to match it's style and color. Also I have some example sites for layout:
matsquick.example
weave-outlet.example

Industry/Entity Type

Carpet

Requirements
Must have
• Scrolling images on front page. I will insert photos, just need the code.

```html
<!DOCTYPE html>
<html lang="en">
<head>
<meta charset="utf-8">
<title>Loom Harbor – Rugs &amp; Carpet</title>
<link href="https://fonts.googleapis.com/css2?family=Open+Sans:wght@400;600&family=Roboto+Condensed:wght@400;700&display=swap" rel="stylesheet">
<style>
:root{
  --bar:#2b2b2b;
  --header:#232323;
  --blue:#1a64b8;
  --sky:#0aa0ea;
  --green:#5aa51c;
  --panel:#2a2a2a;
  --panel-dark:#1e1e1e;
  --page:#f2f2f2;
  --text:#333;
  --muted:#777;
  --line:#d6d6d6;
}
*{box-sizing:border-box;margin:0;padding:0}
html,body{width:918px;height:1200px;overflow:hidden}
body{position:relative;background:var(--page);font-family:"Roboto Condensed",sans-serif;color:var(--text)}
a{color:inherit;text-decoration:none}

/* top bar */
.topbar{position:absolute;left:0;top:0;width:918px;height:24px;background:var(--bar);border-bottom:1px solid #444;font:600 8px "Open Sans",sans-serif;color:#ddd;text-transform:uppercase}
.topbar .home{position:absolute;left:73px;top:3px;width:46px;height:18px;background:var(--blue);color:#fff;line-height:18px;text-align:center}
.topbar .left a{position:absolute;top:0;line-height:24px}
.topbar .right{position:absolute;right:78px;top:0;line-height:24px;display:flex;gap:6px}
.topbar .right .sep{color:#888}
.caret{display:inline-block;border:3px solid transparent;border-top:4px solid #fff;margin-left:5px;vertical-align:-1px}

/* header */
.header{position:absolute;left:0;top:25px;width:918px;height:80px;background:var(--header)}
.brand{position:absolute;left:82px;top:20px;display:flex;align-items:center;gap:10px}
.brand .mark{width:34px;height:34px;border-radius:50%;background:#fff}
.brand .name{font:700 30px "Roboto Condensed",sans-serif;color:#fff;letter-spacing:.5px}
.search{position:absolute;left:645px;top:15px;width:190px;height:17px;background:#fff;border:1px solid #ccc;font:9px "Open Sans",sans-serif;color:#999;padding-left:6px;line-height:15px}
.search svg{position:absolute;right:5px;top:3px}
.cart{position:absolute;right:83px;top:49px;font:600 9px "Open Sans",sans-serif;color:#fff;display:flex;align-items:center;gap:4px}
.cart small{font-size:7px;color:#aaa;font-weight:400}

/* hero */
.hero{position:absolute;left:0;top:105px;width:918px;height:406px;background:linear-gradient(180deg,#e9e9e9,#f6f6f6 50%,#e4e4e4)}
.slide{position:absolute;left:70px;top:9px;width:776px;height:327px;background:linear-gradient(160deg,#6f9ad6 0%,#a9c2e6 30%,#d9cfb6 60%,#efe6cf 100%)}
.slide-caption{position:absolute;right:22px;bottom:24px;text-align:right;font-family:"Roboto Condensed",sans-serif;font-weight:700;line-height:1}
.slide-caption .l1{color:var(--green);font-size:20px}
.slide-caption .l2{color:var(--blue);font-size:30px;margin-top:2px}
.thumbs{position:absolute;left:71px;top:343px;display:flex;gap:25px}
.thumb{width:135px;height:57px}

/* sidebar */
.sidebar{position:absolute;left:70px;top:531px;width:185px;height:495px;background:var(--panel)}
.side-head{height:27px;background:var(--panel-dark);color:#ddd;font-size:15px;line-height:27px;padding-left:15px;position:relative}
.side-head::before{content:"";position:absolute;left:6px;top:10px;border:4px solid transparent;border-left:4px solid #ccc}
.cat-active{margin-top:3px;height:25px;background:var(--green);color:#fff;font-size:12px;line-height:25px;padding-left:31px;position:relative}
.cat-active::before{content:"";position:absolute;left:17px;top:9px;width:7px;height:7px;background:#fff}
.sub{list-style:none;margin:0 6px 0 32px}
.sub li{height:26px;line-height:26px;font-size:10px;color:#ddd;border-bottom:1px dashed #555;position:relative}
.sub li svg{position:absolute;left:-17px;top:9px}
.cats{list-style:none;margin-top:12px;background:#262626;padding:5px 0 12px}
.cats li{height:28px;line-height:28px;font-size:12px;color:#eee;padding-left:31px;position:relative}
.cats li::before{content:"";position:absolute;left:17px;top:11px;width:6px;height:6px;background:#999}
.login-head{margin-top:12px;border-top:1px solid #3a3a3a}
.field{margin:12px 0 0 11px;width:159px;height:24px;border:1px solid #555;border-radius:3px;background:#1c1c1c;color:#ddd;font-size:10px;line-height:22px;padding-left:9px}
.field+.field{margin-top:8px}
.login-row{display:flex;align-items:center;margin:9px 0 0 14px}
.btn-login{width:46px;height:18px;background:var(--green);color:#fff;font-size:10px;line-height:18px;text-align:center;border-radius:2px;flex:none}
.forgot{margin-left:25px;font-size:10px;color:#ddd;white-space:nowrap}
.create{margin-top:12px;text-align:center;font-weight:700;font-size:10px;color:#fff;letter-spacing:.3px}

/* content */
.content{position:absolute;left:285px;top:531px;width:551px}
.welcome{font-size:23px;color:var(--blue);padding-bottom:1px;border-bottom:2px solid #bbb;width:545px;font-weight:400}
.welcome b{color:var(--green);font-weight:700;letter-spacing:.5px}
.intro{margin-top:14px;font-size:10.2px;line-height:17px;color:#444;text-align:justify;width:550px}
.intro+.intro{margin-top:17px}
.more{display:block;margin:16px auto 0;width:147px;height:22px;background:var(--sky);border:2px solid #7cc9f2;color:#fff;font-size:10px;text-align:center;line-height:18px;box-shadow:0 0 0 1px #1a7fc0}
.dashed{margin-top:16px;border-top:1px dashed #ccc}
.special{margin-top:12px;font-size:18px;color:var(--blue);padding-left:3px;font-weight:400}
.special b{color:var(--green)}
.products{position:absolute;left:-2px;top:286px;display:flex;gap:12px}
.card{width:177px;height:211px;background:#fff;border:1px solid #e1e1e1;position:relative;text-align:center}
.card .pic{position:absolute;top:13px;left:50%;transform:translateX(-50%)}
.card .title{position:absolute;top:128px;width:100%;font-size:10.5px;color:#222}
.card .price{position:absolute;top:145px;width:100%;font:600 8px "Open Sans",sans-serif;color:var(--sky)}
.card .rule{position:absolute;top:162px;left:13px;right:13px;border-top:1px solid #ddd}
.card .actions{position:absolute;top:175px;left:13px;display:flex}
.card .info{width:72px;height:20px;background:#eee;font:italic 10px "Open Sans",sans-serif;color:#555;line-height:20px}
.card .add{width:76px;height:20px;background:var(--sky);font:10px "Open Sans",sans-serif;color:#fff;line-height:20px}

/* footer */
.footer{position:absolute;left:0;top:1039px;width:918px;height:118px;background:#fff;border-top:4px solid #e6e6e6}
.foot-brand{position:absolute;left:82px;top:34px;display:flex;align-items:center;gap:10px}
.foot-brand .mark{width:30px;height:30px;border-radius:50%;background:#222}
.foot-brand .name{font:700 26px "Roboto Condensed",sans-serif;color:#333}
.col{position:absolute;top:20px}
.col h4{font-weight:400;font-size:12px;color:#333;margin-bottom:6px}
.col li{list-style:none;font:7.5px "Open Sans",sans-serif;color:#666;line-height:17px}
.col li::before{content:"";display:inline-block;border:2px solid transparent;border-left:3px solid #666;margin-right:2px}
.pay{position:absolute;left:677px;top:41px;display:flex;gap:10px}
.pay span{width:33px;height:19px;border:1px solid #ccc;background:#f4f4f4;position:relative}
.pay span::after{content:"";position:absolute;left:6px;top:6px;width:19px;height:6px;background:var(--c)}
.social{position:absolute;left:690px;top:77px;display:flex;gap:10px}
.social span{width:26px;height:26px;border-radius:50%;background:var(--c);border:2px solid #e4e4e4;box-shadow:0 1px 2px #999}
.copy{position:absolute;left:0;top:1157px;width:918px;height:43px;background:#fff;border-top:1px solid #eee;text-align:center;font:8px "Open Sans",sans-serif;color:#666;line-height:38px}
</style>
</head>
<body>

<div class="topbar">
  <a class="home" href="#">Home</a>
  <div class="left"><a href="#" style="left:136px">About Us</a><a href="#" style="left:204px">Contact Us</a></div>
  <div class="right">
    <a href="#">My Account</a><span class="sep">|</span>
    <a href="#">Shopping Cart</a><span class="sep">|</span>
    <a href="#">Checkout</a><span class="sep">|</span>
    <a href="#" style="margin-left:4px">Login/Register Now</a>
    <span style="margin-left:10px">EN<i class="caret"></i></span>
    <span style="margin-left:16px">$<i class="caret"></i></span>
  </div>
</div>

<header class="header">
  <div class="brand"><span class="mark"></span><span class="name">Loom Harbor</span></div>
  <div class="search">Search
    <svg width="9" height="9" viewBox="0 0 10 10"><circle cx="4" cy="4" r="3" fill="none" stroke="#777" stroke-width="1.4"/><line x1="6.3" y1="6.3" x2="9" y2="9" stroke="#777" stroke-width="1.6"/></svg>
  </div>
  <div class="cart">
    <svg width="18" height="14" viewBox="0 0 18 14"><path d="M0 1h3l2 8h10l2-6H5" fill="none" stroke="#3fbf2a" stroke-width="2"/><rect x="5" y="3" width="11" height="5" fill="#3fbf2a"/><circle cx="7" cy="12" r="1.6" fill="#3fbf2a"/><circle cx="14" cy="12" r="1.6" fill="#3fbf2a"/></svg>
    CART : <small>0 item(s) - $0.00</small>
  </div>
</header>

<section class="hero">
  <div class="slide" role="img" aria-label="Two children and a golden dog resting on a cream shag carpet under a blue blanket">
    <div class="slide-caption"><div class="l1">LATEST COLLECTION WITH</div><div class="l2">VARIETY OF DESIGNS</div></div>
  </div>
  <div class="thumbs">
    <div class="thumb" role="img" aria-label="Children and dog on carpet" style="background:linear-gradient(135deg,#7e9fcf,#e2d6bd)"></div>
    <div class="thumb" role="img" aria-label="Living room with patterned area rug" style="background:linear-gradient(135deg,#ede8e0,#8a5a48 60%,#c9c0b4)"></div>
    <div class="thumb" role="img" aria-label="Furnished lounge with carpeted floor" style="background:linear-gradient(135deg,#3e3a36,#8a7560 50%,#cdbfa9)"></div>
    <div class="thumb" role="img" aria-label="Dog lying on beige plush carpet" style="background:linear-gradient(135deg,#d8c6a4,#bfa57c 60%,#a37c4e)"></div>
    <div class="thumb" role="img" aria-label="Modern room with red rug and sofa" style="background:linear-gradient(135deg,#c9c9c9,#cc2a2a 55%,#8f1414)"></div>
  </div>
</section>

<aside class="sidebar">
  <div class="side-head">Shop by Category</div>
  <div class="cat-active">Commercial Flooring</div>
  <ul class="sub">
    <li><svg width="9" height="8" viewBox="0 0 9 8"><path d="M1 4l2.5 2.5L8 1" fill="none" stroke="#5aa51c" stroke-width="1.6"/></svg>Carpet Tiles</li>
    <li><svg width="9" height="8" viewBox="0 0 9 8"><path d="M1 4l2.5 2.5L8 1" fill="none" stroke="#5aa51c" stroke-width="1.6"/></svg>Carpet Roll</li>
  </ul>
  <ul class="cats">
    <li>Carpet Flooring</li>
    <li>Harwood Floorings</li>
    <li>Area Rugs</li>
  </ul>
  <div class="side-head login-head">Login Area</div>
  <div class="field">Email Address</div>
  <div class="field">********</div>
  <div class="login-row"><span class="btn-login">Login</span><span class="forgot">Forgot Password??</span></div>
  <div class="create">CREATE NEW ACCOUNT</div>
</aside>

<main class="content">
  <h1 class="welcome">Welcome to <b>LOOM HARBOR</b></h1>
  <p class="intro">Contrary to popular belief, Lorem Ipsum is not simply random text. It has roots in a piece of classical Latin literature from 45 BC, making it over 2000 years old. Arthur Penwell, a Latin professor at Brookfield Valley College in Virginia, looked up one of the more obscure Latin words, consectetur, from a Lorem Ipsum passage, and going through the cites of the word in classical literature, discovered the undoubtable source. Lorem Ipsum comes from sections 1.10.32 and 1.10.33 of "de Rebus Aurelianis" (On Golden Matters) by Varenius Dol, written in 45 BC.</p>
  <p class="intro">This book is a treatise on the theory of ethics, very popular during the Renaissance. The first line of Lorem Ipsum, "Lorem ipsum dolor sit amet..", comes from a line in section.The standard chunk of Lorem Ipsum used since the 1500s is reproduced below for those interested....</p>
  <a class="more" href="#">Click Here For More Details</a>
  <div class="dashed"></div>
  <h2 class="special">Today's <b>SPECIAL</b></h2>

  <div class="products">
    <div class="card">
      <div class="pic" role="img" aria-label="Dark mahogany hardwood plank sample" style="width:106px;height:100px;background:linear-gradient(135deg,#4a2415,#8a4a2c 45%,#5a2c18)"></div>
      <div class="title">Harbor Walnut Mocha</div>
      <div class="price">From $7.69 to $7.89</div>
      <div class="rule"></div>
      <div class="actions"><span class="info">more info</span><span class="add">add to cart</span></div>
    </div>
    <div class="card">
      <div class="pic" role="img" aria-label="Traditional patterned brown and gold area rug" style="top:18px;width:134px;height:88px;background:radial-gradient(ellipse,#5a3a22 30%,#3e2616 60%,#c9b07a 88%)"></div>
      <div class="title">Heritage 7702-31</div>
      <div class="price">From $79.00 to $1,699.00</div>
      <div class="rule"></div>
      <div class="actions"><span class="info">more info</span><span class="add">add to cart</span></div>
    </div>
    <div class="card">
      <div class="pic" role="img" aria-label="Navy commercial carpet tile sample" style="width:101px;height:101px;background:#3b3d5c"></div>
      <div class="title">lh-ct-31027458-180</div>
      <div class="price">Call for Pricing</div>
      <div class="rule"></div>
      <div class="actions"><span class="info">more info</span><span class="add">add to cart</span></div>
    </div>
  </div>
</main>

<footer class="footer">
  <div class="foot-brand"><span class="mark"></span><span class="name">Loom Harbor</span></div>
  <div class="col" style="left:310px"><h4>Information</h4><ul><li>About Us</li><li>Shipping Policy</li><li>Privacy Policy</li></ul></div>
  <div class="col" style="left:422px"><h4>Customer Service</h4><ul><li>Contact Us</li><li>Sitemap</li><li>Cart Help</li></ul></div>
  <div class="col" style="left:549px"><h4>My Account</h4><ul><li>My Account</li><li>Order History</li><li>Wishlist</li></ul></div>
  <div class="col" style="left:677px"><h4>We Accept Only</h4></div>
  <div class="pay" aria-label="Accepted payment methods">
    <span style="--c:#1a3a8a"></span><span style="--c:#d8402a"></span><span style="--c:#e37a1e"></span><span style="--c:#2a6bb8"></span>
  </div>
  <div class="social" aria-label="Social links">
    <span style="--c:#2aa3e0"></span><span style="--c:#d9402e"></span><span style="--c:#c4151c"></span><span style="--c:#5d7fb8"></span>
  </div>
</footer>
<div class="copy">© 2014 Loom Harbor, LLC</div>

</body>
</html>
```